Quorva - corporate Business Card

We need a good look and innovative business card for a new start up company based in Los Angeles called "Quorva". We are in a payment business, including payment card, app, and ewallet. We are expert in online payment and Card not present (CNP) transaction.
We need an innovative, modern business card.

Our logo font is Aero Matics

Target Market(s)

Startup - Bank - Online Payment - Card Manufacturing

Industry/Entity Type

Startup

Contact Information for Business Card

phone: 555 014 7396 - Address: 4172 Marlowe blvd, Larkfield, NV 90299

Requirements
Must have
• Message: innovative, professional, expert, high tech, trust, online payment expert, security
Nice to have
• no comment
Should not have
• no Comment

```html
<!DOCTYPE html>
<html lang="en">
<head>
<meta charset="utf-8">
<title>Quorva – Business Card</title>
<link href="https://fonts.googleapis.com/css2?family=Exo+2:wght@600&family=Open+Sans:wght@400;700&display=swap" rel="stylesheet">
<style>
  :root {
    --stage: #1c1c1c;
    --brand-red: #b72030;
    --paper: #ffffff;
    --blush: #f6e4df;
    --ink-grey: #8a8a8a;
  }
  * { margin: 0; padding: 0; box-sizing: border-box; }
  html, body { width: 1200px; height: 741px; overflow: hidden; }
  body {
    background: var(--stage);
    position: relative;
    font-family: "Open Sans", Arial, sans-serif;
  }
  .card {
    position: absolute;
    top: 229px;
    width: 494px;
    height: 282px;
    border-radius: 10px;
    overflow: hidden;
  }
  .card--front { left: 100px; background: var(--brand-red); }
  .card--back { left: 606px; background: var(--paper); }

  .brand-dot {
    position: absolute;
    border-radius: 50%;
  }
  .brand-name {
    position: absolute;
    font-family: "Exo 2", Arial, sans-serif;
    font-weight: 600;
    line-height: 1;
    white-space: nowrap;
  }

  .card--front .brand-dot {
    left: 108px; top: 99px; width: 84px; height: 84px;
    background: var(--paper);
  }
  .card--front .brand-name {
    left: 205px; top: 107px;
    font-size: 54px;
    color: var(--paper);
  }

  .back-decor {
    position: absolute;
    left: -1px; top: -52px;
    width: 222px; height: 222px;
    border-radius: 50%;
    background: var(--blush);
  }
  .card--back .brand-dot {
    left: 24px; top: 197px; width: 60px; height: 60px;
    background: var(--brand-red);
  }
  .card--back .brand-name {
    left: 91px; top: 203px;
    font-size: 38px;
    color: var(--brand-red);
  }

  .contact {
    position: absolute;
    left: 324px; top: 155px;
    color: var(--ink-grey);
    font-size: 13.5px;
    line-height: 16px;
  }
  .contact__name {
    color: var(--brand-red);
    font-weight: 700;
    font-size: 18px;
    line-height: 18px;
  }
  .contact__role { font-size: 14px; line-height: 14px; }
  .contact__address { margin-top: 12px; }
  .contact__phone { margin-top: 10px; }
  .contact__label { color: var(--brand-red); font-weight: 700; }
</style>
</head>
<body>
  <section class="card card--front" aria-label="Card front">
    <span class="brand-dot"></span>
    <span class="brand-name">quorva</span>
  </section>

  <section class="card card--back" aria-label="Card back">
    <span class="back-decor"></span>
    <span class="brand-dot"></span>
    <span class="brand-name">quorva</span>
    <div class="contact">
      <p class="contact__name">Dana Reyes</p>
      <p class="contact__role">Managing Director</p>
      <p class="contact__address">4172 Marlowe blvd,<br>Larkfield, NV 90299</p>
      <p class="contact__phone"><span class="contact__label">P:</span> 555 014 7396</p>
    </div>
  </section>
</body>
</html>
```